Norvane Website Design (New Start Up Investment Management Firm)

We need a website designed. We have attached a Powerpoint with our proposed website content (which is quite minimal), the format is just a suggestion but we would like to see your alternative and improved ideas. We are a boutique investment firm so are looking for something sleek and professional. I have included on the last page of the attachment our brand colours and font styles as well as attaching our logo design. We would like the successful designer to design the website and build the buttons etc.

On the "Contact Us" page, we are open to suggestions on how best to show the map, whether is should be static or open a google maps page. We would like the phone number and email address to be set up so people can click on them on their phone and it calls us or emails us directly.

We would prefer not to have photos of landscapes on the site.
Our website is hosted on a Linux based website.

We would also like 3 links at the bottom of each page for links to pdfs:
- Disclaimer, Terms and Conditions of Web Site Use
- Stewardship
- Pillar III

Target Market(s)

Institutional Investors

Industry/Entity Type

Investment

Coding

Coded - Design and coding required

Number of Pages Required

3 page

Font styles to use
Other font styles liked:
• Logo: Lato, Text: Source Sans Pro

Colors

Designer to choose colors to be used in the design.

Requirements
Must have
• The website must use the colours and fonts on the last page of the attached powerpoint. I can't see an option to select the exact colour palette below so please look at the PPT.
• For others please see Project description.
Should not have
• Landscape photos

```html
<!DOCTYPE html>
<html lang="en">
<head>
<meta charset="utf-8">
<title>Norvane Investment Management</title>
<link rel="stylesheet" href="https://fonts.googleapis.com/css2?family=Lato:wght@400;700&display=swap">
<style>
:root{
  --navy:#0b2d63;
  --brand-blue:#0a3a9a;
  --sky:#6fb3e6;
  --text:#222;
  --muted:#7a7a7a;
  --rule:#dcdcdc;
  --band:#f3f3f3;
  --footer:#1e202b;
  --footer-text:#a9abb4;
}
*{box-sizing:border-box;margin:0;padding:0}
html,body{width:1200px;height:1064px;overflow:hidden;background:#fff}
body{font-family:"Lato",sans-serif;color:var(--text);position:relative}
.site-header{position:absolute;top:0;left:0;width:1200px;height:117px}
.brand{position:absolute;left:132px;top:36px;display:flex;align-items:center;gap:12px}
.brand-mark{width:44px;height:44px;background:var(--navy)}
.brand-name{font-size:38px;font-weight:400;color:var(--navy);letter-spacing:1px;line-height:1}
.header-phone{position:absolute;right:132px;top:28px;font-size:17px;color:#222;display:flex;align-items:center;gap:6px}
.main-nav{position:absolute;right:132px;top:72px;display:flex;gap:28px;font-size:12px}
.main-nav a{color:#555;text-decoration:none}
.main-nav a.active{color:var(--brand-blue)}
.hero{position:absolute;top:117px;left:0;width:1200px;height:400px}
.hero-image{position:absolute;inset:0;background:linear-gradient(100deg,#cfded6 0%,#e6e8df 40%,#ebe3d4 65%,#d9b79a 85%,#e4c0a4 100%)}
.hero-copy{position:absolute;left:133px;top:106px;width:400px}
.hero-welcome{font-size:26px;font-weight:400;color:var(--brand-blue);line-height:30px}
.hero-title{font-size:26px;font-weight:700;color:var(--brand-blue);line-height:32px;margin-bottom:6px;white-space:nowrap}
.hero-text{font-size:12.5px;line-height:19px;color:#222}
.intro{position:absolute;top:574px;left:132px;width:936px;text-align:center;font-size:15.5px;line-height:24px;color:#222}
.tabs-rule{position:absolute;top:702px;left:132px;width:936px;border-top:1px solid var(--rule)}
.tabs{position:absolute;top:706px;left:438px;display:flex;gap:3px}
.tab{width:160px;height:44px;display:flex;align-items:center;justify-content:center;font-size:17px;color:#fff;position:relative}
.tab-active{background:var(--navy)}
.tab-active::after{content:"";position:absolute;bottom:-9px;left:50%;margin-left:-9px;border-left:9px solid transparent;border-right:9px solid transparent;border-top:9px solid var(--navy)}
.tab-inactive{background:var(--sky)}
.tab-panel{position:absolute;top:774px;left:132px;width:936px;text-align:center;font-size:15.5px;line-height:24px;color:var(--muted)}
.contact-band{position:absolute;top:900px;left:0;width:1200px;height:68px;background:var(--band);font-size:15px;color:#555}
.contact-item{position:absolute;top:23px;display:flex;align-items:center;gap:7px}
.contact-address{left:132px}
.contact-phone{left:603px}
.contact-email{right:132px}
.site-footer{position:absolute;top:968px;left:0;width:1200px;height:96px;background:var(--footer);font-size:11px;color:var(--footer-text)}
.footer-nav{position:absolute;left:132px;top:27px}
.footer-legal{position:absolute;left:132px;top:54px}
.site-footer a{color:var(--footer-text);text-decoration:none}
.sep{margin:0 7px}
.social{position:absolute;right:132px;top:35px;display:flex;gap:7px}
.social span{width:26px;height:26px;border-radius:50%;background:#3d6fb8;display:block}
</style>
</head>
<body>
<header class="site-header">
  <div class="brand"><span class="brand-mark"></span><span class="brand-name">NORVANE</span></div>
  <div class="header-phone">
    <svg width="9" height="13" viewBox="0 0 9 13"><rect x="1" y="0.8" width="7" height="11.4" rx="1.2" fill="none" stroke="#222" stroke-width="1.5"/><rect x="2.5" y="2.5" width="4" height="6" fill="#222"/></svg>
    555 014 2290
  </div>
  <nav class="main-nav">
    <a class="active" href="#">Home</a><a href="#">About Us</a><a href="#">Services</a><a href="#">Solutions</a><a href="#">Contact Us</a>
  </nav>
</header>

<section class="hero">
  <div class="hero-image" role="img" aria-label="Cupped hands holding a pile of coins with young green seedlings growing from them"></div>
  <div class="hero-copy">
    <h2 class="hero-welcome">Welcome to</h2>
    <h1 class="hero-title">NORVANE INVESTMENT MANAGEMENT</h1>
    <p class="hero-text">Norvane Investment Management was founded in 2016 with a clear vision to create an independent and nimble firm focused on generating superior risk-adjusted returns.</p>
  </div>
</section>

<p class="intro">Norvane has designed an innovative investment approach which aims to harness the best elements of alternative investment management whilst reducing its recognised shortcomings. We are a performance and client focused firm, committed to building lasting relationships, treating our clients like partners rather than revenue streams.</p>

<div class="tabs-rule"></div>
<div class="tabs">
  <div class="tab tab-active">Our Approach</div>
  <div class="tab tab-inactive">Our Philosophy</div>
</div>
<p class="tab-panel">Norvane’ philosophy is based on the understanding that financial markets tend to mean revert and that valuations and fundamentals matter. Norvane strives to construct a resilient portfolio diversified across asset classes, strategies and time horizons to achieve our target return objective. Freedom of idea expression enables us to react nimbly to market dislocations.</p>

<section class="contact-band">
  <div class="contact-item contact-address">
    <svg width="8" height="12" viewBox="0 0 8 12"><path d="M4 0a4 4 0 0 0-4 4c0 3 4 8 4 8s4-5 4-8a4 4 0 0 0-4-4zm0 5.5a1.5 1.5 0 1 1 0-3 1.5 1.5 0 0 1 0 3z" fill="#666"/></svg>
    14 Harrowden Place, London W1 4QT, United Kingdom
  </div>
  <div class="contact-item contact-phone">
    <svg width="11" height="11" viewBox="0 0 11 11"><path d="M2.2 0.5l2 2.3-1 1.4c.6 1.4 1.8 2.6 3.3 3.3l1.4-1 2.3 2-1 2C4.6 10.5.5 6.4.5 1.5z" fill="#666"/></svg>
    +44 20 5550 0187
  </div>
  <div class="contact-item contact-email">
    <svg width="12" height="9" viewBox="0 0 12 9"><rect width="12" height="9" fill="#666"/><path d="M0 0l6 5 6-5" fill="none" stroke="#f3f3f3" stroke-width="1.2"/></svg>
    clientservices@norvaneim.example
  </div>
</section>

<footer class="site-footer">
  <div class="footer-nav">
    <a href="#">Home</a><span class="sep">|</span><a href="#">About Us</a><span class="sep">|</span><a href="#">Services</a><span class="sep">|</span><a href="#">Solutions</a><span class="sep">|</span><a href="#">Contact Us</a><span class="sep">|</span><a href="#">Stewardship</a><span class="sep">|</span><a href="#">Pillar III</a>
  </div>
  <div class="footer-legal">
    Copyright © 2017 Norvane. All rights reserved.<span style="margin-left:14px"></span><a href="#">Disclaimer</a><span class="sep">|</span><a href="#">Terms and Conditions</a>
  </div>
  <div class="social" aria-label="Social links">
    <span></span><span></span><span></span>
  </div>
</footer>
</body>
</html>
```